Website design for a hair building fibre

Hi I’m needing a website made for both men and women to purchase the product is a hair building fibre that you apply to thinning hair to make your hair look really thick I’ll need the website to be easy to use professional and also very classy I will need it to work with lumen split tok fund and credit cards I’ll need to have the CEO words and everything ready so I can sell I don’t have photos that I want to put on there so I’ll need a website designer to assist me in having the beautiful photos on there I know very little about websites so I need someone to be able to do it all for me

I can only provide photos of the colours of the products
I believe there will be 8 colours to sell as well
I’ve uploaded a photo of the logo I’d really like it if the website designer can check other competitors website so my website does not look like theres, I don’t want my website to look like a copied website of the competitors I’m located in Australia.
I’m also looking for someone who can open up a Palvista and Glimmerly page and then can unload photos on them ready for consumers to view and buy.

```html
<!DOCTYPE html>
<html lang="en">
<head>
<meta charset="utf-8">
<title>Strandfull – Hair Building Fibre</title>
<link href="https://fonts.googleapis.com/css2?family=Poppins:ital,wght@0,300;0,400;0,500;0,600;0,700;0,800;1,400&display=swap" rel="stylesheet">
<style>
:root{
  --ink:#13202c;
  --navy:#1f2c3b;
  --slate:#2f3c4b;
  --sky:#6cc4e6;
  --accent:#3a9fc4;
  --logo:#5fa9c9;
  --text:#3b3b3b;
  --muted:#6d6d6d;
  --hero-bg:#e7e6ee;
  --card-img:#efefef;
  --white:#ffffff;
  --line:#d9d9d9;
}
*{margin:0;padding:0;box-sizing:border-box}
html,body{width:1200px;height:3537px;overflow:hidden}
body{font-family:'Poppins',sans-serif;color:var(--text);background:var(--white);position:relative}
section,header,footer{position:relative;width:1200px;overflow:hidden}
.abs{position:absolute}
.nowrap{white-space:nowrap}

/* Hero */
.hero{height:699px;background:linear-gradient(90deg,#e9e8ef 0%,#e3e2ea 60%,#dcd9e2 100%)}
.hero-photo{position:absolute;left:590px;top:0;width:610px;height:699px;background:radial-gradient(ellipse at 60% 45%,#c9a48c 0%,#8a5a3e 35%,#d8d4dc 75%,#e3e2ea 100%)}
.brand{position:absolute;left:107px;top:22px;font-size:30px;font-weight:300;letter-spacing:1px;color:var(--logo)}
.nav{position:absolute;left:549px;top:34px;display:flex;gap:30px;font-size:14.5px;color:#2a2a2a}
.nav .active{color:var(--sky)}
.nav-icons{position:absolute;left:1006px;top:37px;display:flex;gap:10px}
.hero-circle{position:absolute;left:474px;top:117px;width:210px;height:210px;border-radius:50%;background:var(--white)}
.bottle{position:absolute;border-radius:6px}
.hero-title{position:absolute;left:106px;top:285px;font-size:84px;font-weight:700;color:var(--ink);letter-spacing:-1px;line-height:1}
.hero-text{position:absolute;left:112px;top:387px;font-size:14.5px;line-height:31px;color:#2b2b2b;white-space:nowrap}
.btn{position:absolute;display:flex;align-items:center;justify-content:center;font-weight:600;font-size:14.5px;color:var(--white);border-radius:4px}
.btn-sky{background:var(--sky);box-shadow:0 4px 8px rgba(0,0,0,.12)}
.btn-dark{background:var(--ink);box-shadow:0 4px 8px rgba(0,0,0,.15)}
.dots{position:absolute;display:flex;gap:4px}
.dot{width:12px;height:12px;border-radius:50%;border:1.5px solid #333}
.dot.on{background:#222}
.dots.light .dot{border-color:#fff}
.dots.light .dot.on{background:#fff}

/* About */
.about{height:679px}
.about-img{position:absolute;left:111px;top:95px;width:441px;height:504px;background:linear-gradient(90deg,#8a7a6c 0%,#d9d2cc 45%,#fff 50%,#d0cbc6 55%,#5a5048 100%);box-shadow:0 0 10px rgba(0,0,0,.1)}
.h2{font-weight:700;color:var(--ink);font-size:40px;line-height:1}
.rule{position:absolute;height:2px;width:84px;background:var(--accent)}
.about-copy{position:absolute;left:600px;top:203px;font-size:12.5px;line-height:31px;color:#444;white-space:nowrap}
.about-copy p+p{margin-top:11px}

/* Products */
.products{height:662px;background:linear-gradient(180deg,#34414f 0%,#2c3845 55%,#3b4654 100%)}
.card{position:absolute;top:165px;width:298px;height:429px;background:var(--white);border-radius:70px 70px 4px 4px;overflow:hidden}
.card-img{position:absolute;left:8px;top:8px;width:282px;height:197px;background:var(--card-img);border-radius:64px 64px 0 0}
.card h3{position:absolute;top:226px;width:100%;text-align:center;font-size:18px;font-weight:500;color:#1a1a1a}
.card p{position:absolute;top:261px;left:0;right:0;text-align:center;font-size:11.5px;line-height:27px;color:var(--muted);white-space:nowrap}
.card .btn{left:76px;top:359px;width:146px;height:43px}
.circ-arrow{position:absolute;width:36px;height:36px;border:1.5px solid #fff;border-radius:50%}

/* Benefits */
.benefits{height:604px}
.icon-c{position:absolute;width:50px;height:50px;border-radius:50%;background:var(--navy)}
.ben{position:absolute;width:300px}
.ben h4{font-size:14.5px;font-weight:600;color:#1a1a1a}
.ben p{margin-top:8px;font-size:11.5px;line-height:26px;color:var(--muted);white-space:nowrap}
.ben.right{text-align:right}

/* Reviews */
.reviews{height:431px;background:linear-gradient(180deg,#1c2837,#233142)}
.quote{position:absolute;left:0;top:152px;width:1200px;text-align:center;font-style:italic;font-size:13px;line-height:31px;color:#e8ecf0;white-space:nowrap}
.reviewer{position:absolute;top:285px;width:100%;text-align:center;color:#fff;font-size:21px}
.reviewer-role{position:absolute;top:320px;width:100%;text-align:center;color:#dfe4ea;font-size:12.5px}

/* Footer */
.footer{height:462px}
.fcol{position:absolute;top:83px}
.fcol h5{font-size:14.5px;font-weight:500;color:var(--navy);letter-spacing:.3px}
.fcol .rule{width:30px;margin-top:8px;position:static}
.fcol ul{list-style:none;margin-top:20px;font-size:13.5px;color:#333}
.fcol li{line-height:30px}
.fcol.tight li{line-height:23px}
.news-text{font-size:13.5px;line-height:24px;color:#333;margin-top:20px;white-space:nowrap}
.email{position:absolute;left:813px;top:193px;width:277px;height:40px;border:1px solid #bbb;border-radius:20px;font-size:12px;color:#222;padding:10px 20px}
.send{position:absolute;right:16px;top:10px;width:19px;height:19px;border-radius:50%;background:var(--ink)}
.social{position:absolute;top:262px;width:48px;height:48px;border:1px solid #777;border-radius:50%;display:flex;align-items:center;justify-content:center;font-size:8px;color:#333}
.divider{position:absolute;left:111px;top:349px;width:976px;height:1px;background:var(--line)}
.copyright{position:absolute;left:117px;top:387px;font-size:14px;color:#222}
.pay{position:absolute;top:385px;left:498px;display:flex;gap:9px}
.pay span{width:33px;height:22px;border:1px solid #ccc;border-radius:2px;font-size:6px;color:#333;display:flex;align-items:center;justify-content:center}
.legal{position:absolute;right:114px;top:389px;font-size:12.5px;color:#222}
</style>
</head>
<body>

<header class="hero">
  <div class="hero-photo" role="img" aria-label="Photo of a smiling woman with long wavy brown hair"></div>
  <div class="brand">Strandfull</div>
  <nav class="nav">
    <span class="active">Home</span><span>About Us</span><span>Shop</span><span>Reviews</span><span>Blog</span><span>Contact</span>
  </nav>
  <div class="nav-icons">
    <svg width="13" height="13" viewBox="0 0 13 13"><circle cx="5.5" cy="5.5" r="4" fill="none" stroke="#222" stroke-width="1.8"/><line x1="8.5" y1="8.5" x2="12" y2="12" stroke="#222" stroke-width="2"/></svg>
    <svg width="11" height="13" viewBox="0 0 11 13"><circle cx="5.5" cy="3.5" r="3" fill="#222"/><path d="M0 13c0-4 2.5-6 5.5-6s5.5 2 5.5 6z" fill="#222"/></svg>
    <svg width="14" height="13" viewBox="0 0 14 13"><path d="M0 1h3l2 7h7l2-6H4" fill="none" stroke="#222" stroke-width="1.8"/><circle cx="6" cy="11" r="1.5" fill="#222"/><circle cx="11" cy="11" r="1.5" fill="#222"/></svg>
  </div>
  <div class="hero-circle"></div>
  <div class="bottle" role="img" aria-label="Silver hair fibre bottle, brown shade" style="left:543px;top:98px;width:71px;height:241px;background:linear-gradient(90deg,#9a9a9a,#f4f4f4 40%,#cfcfcf 70%,#8d8d8d)"></div>
  <svg class="abs" style="left:22px;top:340px" width="38" height="20" viewBox="0 0 38 20"><path d="M37 10H3M11 2L2 10l9 8" fill="none" stroke="#111" stroke-width="2"/></svg>
  <svg class="abs" style="left:1110px;top:348px" width="38" height="20" viewBox="0 0 38 20"><path d="M1 10h34M27 2l9 8-9 8" fill="none" stroke="#111" stroke-width="2"/></svg>
  <h1 class="hero-title">Strandfull</h1>
  <p class="hero-text">Lorem ipsum dolor sit amet, consectetur adipiscing elit, sed do<br>eiusmod tempor incididunt ut labore et dolore magna aliqua.<br>Ut enim ad minim veniam, quis nostrud exercitation</p>
  <div class="btn btn-sky" style="left:111px;top:498px;width:202px;height:58px">Shop Now</div>
  <div class="dots" style="left:111px;top:650px"><i class="dot"></i><i class="dot"></i><i class="dot on"></i><i class="dot"></i></div>
</header>

<section class="about">
  <div class="about-img" role="img" aria-label="Before and after photo of a thinning crown and a fuller head of hair"></div>
  <div class="bottle" role="img" aria-label="Black hair fibre bottle" style="left:307px;top:70px;width:74px;height:244px;background:linear-gradient(90deg,#1e1e1e,#555 40%,#3a3a3a 70%,#111)"></div>
  <h2 class="h2 abs" style="left:602px;top:116px">About Us</h2>
  <div class="rule" style="left:600px;top:176px"></div>
  <div class="about-copy">
    <p>Lorem ipsum dolor sit amet, consectetur adipiscing elit, sed do tempor<br>incididunt ut labore et dolore magna aliqua. Ut enim ad minim veniam, quis<br>nostrud exercitation ullamco laboris nisi ut aliquip ex ea consequat. Duis aute<br>irure dolor in reprehenderit in voluptate velit esse cillum dolore eu fugiat nulla<br>pariatur. Excepteur sint occaecat cupidatat non proident, sunt in culpa qui<br>officia deserunt mollit anim id est laborum</p>
    <p>Lorem ipsum dolor sit amet, consectetur adipiscing elit, sed do tempor<br>incididunt ut labore et dolore magna aliqua. Ut enim ad minim veniam, quis<br>nostrud exercitation ullamco laboris nisi ut aliquip</p>
  </div>
  <div class="btn btn-dark" style="left:600px;top:515px;width:202px;height:59px">Read More</div>
</section>

<section class="products">
  <div class="abs" role="img" aria-label="Dimmed background photo of a woman with long hair by a lake" style="inset:0;background:radial-gradient(ellipse at 45% 20%,rgba(120,90,70,.35),transparent 60%)"></div>
  <h2 class="h2 abs" style="left:0;width:1200px;text-align:center;top:62px;color:#fff">Our Products</h2>
  <div class="rule" style="left:558px;top:123px"></div>
  <div class="circ-arrow" style="left:52px;top:352px"><svg width="36" height="36" viewBox="0 0 36 36"><path d="M20 12l-6 6 6 6" fill="none" stroke="#fff" stroke-width="1.8"/></svg></div>
  <div class="circ-arrow" style="left:1104px;top:352px"><svg width="36" height="36" viewBox="0 0 36 36"><path d="M16 12l6 6-6 6" fill="none" stroke="#fff" stroke-width="1.8"/></svg></div>

  <div class="card" style="left:125px">
    <div class="card-img"></div>
    <div class="bottle" role="img" aria-label="Black hair fibre bottle" style="left:122px;top:20px;width:54px;height:177px;background:linear-gradient(90deg,#2a2a2a,#666 40%,#444)"></div>
    <h3>Product 1</h3>
    <p>Lorem ipsum dolor sit amet, consectetur<br>adipiscing elit, sed do eiusmod incididunt ut<br>labore et dolore magna aliqua.</p>
    <div class="btn btn-dark">Shop Now</div>
  </div>
  <div class="card" style="left:450px">
    <div class="card-img"></div>
    <div class="bottle" role="img" aria-label="Red hair fibre bottle" style="left:122px;top:20px;width:54px;height:177px;background:linear-gradient(90deg,#a90e0e,#e42a2a 40%,#c21515)"></div>
    <h3>Product 2</h3>
    <p>Lorem ipsum dolor sit amet, consectetur<br>adipiscing elit, sed do eiusmod incididunt ut<br>labore et dolore magna aliqua.</p>
    <div class="btn btn-dark">Shop Now</div>
  </div>
  <div class="card" style="left:776px">
    <div class="card-img"></div>
    <div class="bottle" role="img" aria-label="Brown hair fibre bottle" style="left:122px;top:20px;width:54px;height:177px;background:linear-gradient(90deg,#7d1f1f,#b03a3a 40%,#932828)"></div>
    <h3>Product 3</h3>
    <p>Lorem ipsum dolor sit amet, consectetur<br>adipiscing elit, sed do eiusmod incididunt ut<br>labore et dolore magna aliqua.</p>
    <div class="btn btn-dark">Shop Now</div>
  </div>
</section>

<section class="benefits">
  <h2 class="h2 abs" style="left:0;width:1200px;text-align:center;top:51px">Benefits</h2>
  <div class="bottle" role="img" aria-label="Silver hair fibre bottle" style="left:542px;top:143px;width:114px;height:385px;background:linear-gradient(90deg,#a5a5a5,#f6f6f6 40%,#d4d4d4 70%,#9b9b9b)"></div>

  <div class="icon-c" style="left:116px;top:247px"></div>
  <div class="ben" style="left:177px;top:246px"><h4>Lorem ipsum dolor sit amet</h4><p>Lorem ipsum dolor sit amet, consectetur adipiscing<br>elit, sed do eiusmod tempor incididunt ut labore et<br>dolore magna aliqua.</p></div>
  <div class="icon-c" style="left:116px;top:404px"></div>
  <div class="ben" style="left:177px;top:403px"><h4>Lorem ipsum dolor sit amet</h4><p>Lorem ipsum dolor sit amet, consectetur adipiscing<br>elit, sed do eiusmod tempor incididunt ut labore et<br>dolore magna aliqua.</p></div>

  <div class="icon-c" style="left:1031px;top:247px"></div>
  <div class="ben right" style="left:717px;top:246px"><h4>Lorem ipsum dolor sit amet</h4><p>Lorem ipsum dolor sit amet, consectetur adipiscing<br>elit, sed do eiusmod tempor incididunt ut labore et<br>dolore magna aliqua.</p></div>
  <div class="icon-c" style="left:1031px;top:404px"></div>
  <div class="ben right" style="left:717px;top:403px"><h4>Lorem ipsum dolor sit amet</h4><p>Lorem ipsum dolor sit amet, consectetur adipiscing<br>elit, sed do eiusmod tempor incididunt ut labore et<br>dolore magna aliqua.</p></div>
</section>

<section class="reviews">
  <div class="abs" role="img" aria-label="Faint background photo of a man's face" style="inset:0;background:radial-gradient(ellipse at 50% 50%,rgba(70,85,100,.35),transparent 65%)"></div>
  <h2 class="h2 abs" style="left:0;width:1200px;text-align:center;top:59px;color:#fff">Products Reviews</h2>
  <div class="rule" style="left:558px;top:119px"></div>
  <p class="quote">Lorem ipsum dolor sit amet, consectetur adipiscing elit, sed do eiusmod tempor incididunt ut labore et dolore magna aliqua.<br>Ut enim ad minim veniam, quis nostrud exercitation ullamco laboris nisi ut aliquip ex ea commodo consequat. Duis aute<br>irure dolor in reprehenderit in voluptate velit esse cillum dolore eu fugiat nulla pariatur. Excepteur sint occaecat cupidatat<br>non proident, sunt in culpa qui officia deserunt mollit anim id est laborum.</p>
  <div class="reviewer">Mara Lind</div>
  <div class="reviewer-role">Lorem ipsum</div>
  <div class="dots light" style="left:555px;top:369px"><i class="dot"></i><i class="dot"></i><i class="dot"></i><i class="dot"></i><i class="dot on"></i><i class="dot"></i></div>
</section>

<footer class="footer">
  <div class="fcol" style="left:114px"><h5>QUICK LINKS</h5><div class="rule"></div><ul><li>Home</li><li>About Us</li><li>Products</li><li>Reviews</li><li>Blog</li><li>Contact</li></ul></div>
  <div class="fcol" style="left:273px"><h5>LEARN MORE</h5><div class="rule"></div><ul><li>Reviews</li><li>Benefits</li><li>FAQs</li></ul></div>
  <div class="fcol tight" style="left:426px"><h5>ABOUT</h5><div class="rule"></div><ul><li>About Us</li><li>Partners</li><li>Payment Option</li><li>Return Policy</li></ul></div>
  <div class="fcol tight" style="left:575px"><h5>CONTACT</h5><div class="rule"></div><ul><li>Help</li><li>Careers</li></ul></div>
  <div class="fcol" style="left:817px"><h5>NEWSLETTER</h5><div class="rule"></div><p class="news-text">Lorem ipsum dolor sit amet, consectetur<br>adipiscing elit, sed do eiusmod tempor</p></div>
  <div class="email">Enter Email<span class="send"></span></div>
  <div class="social" style="left:821px">Linkfold</div>
  <div class="social" style="left:877px">Palvista</div>
  <div class="social" style="left:934px">Glimmerly</div>
  <div class="divider"></div>
  <div class="copyright">© 2022 Strandfull All Rights Reserved</div>
  <div class="pay"><span>Carda</span><span>Meridian</span><span>Findly</span><span>Amplex</span><span>Paywell</span></div>
  <div class="legal">Terms of use | Privacy Policy</div>
</footer>

</body>
</html>
```